Web page design for a startup, no coding

Quorvix is a Data mining startup helping companies get data from websites. We’re looking to revamp our website to make it more professional and conversation friendly.
I need a designer to design the website in PSD and Once the PSD is done, the HTML design will be awarded as a separate job. We’ll need continues improvements to the design based on the user behaviour in the site and this can be a long term work for the right designer.
Read the details on the attached document
Target Market(s)
Big data, Data Mining
Industry/Entity Type
Business Software
Number of Pages Required
5+ page
Requirements
Must have
- Refer to the doc
Nice to have
- Refer to the doc
Should not have
- Refer to the doc

```html
<!DOCTYPE html>
<html lang="en">
<head>
<meta charset="utf-8">
<title>Quorvix — Structured Data Feeds</title>
<link href="https://fonts.googleapis.com/css2?family=Lato:wght@300;400;700&display=swap" rel="stylesheet">
<style>
:root{
  --blue:#139fe0;
  --blue-deep:#0a8fd2;
  --ink:#333a40;
  --muted:#6a7178;
  --line:#d6dbe0;
  --soft:#eef3f8;
  --grey:#f0f0f0;
  --white:#ffffff;
}
*{box-sizing:border-box;margin:0;padding:0}
html,body{width:1200px;height:3358px;overflow:hidden}
body{font-family:'Lato',Arial,sans-serif;color:var(--ink);background:var(--white);position:relative}
section,header,footer{position:absolute;left:0;width:1200px}

/* Hero */
.hero{top:0;height:703px;color:var(--white);overflow:hidden}
.hero-photo{position:absolute;inset:0;background:linear-gradient(120deg,#5fbde9 0%,#2aa7e3 40%,#1a9be0 70%,#48b4e7 100%)}
.brand{position:absolute;left:98px;top:44px;display:flex;align-items:center;gap:14px;font-size:46px;font-weight:400;letter-spacing:.5px}
.brand-mark{width:44px;height:44px;border:3px solid var(--white)}
.nav{position:absolute;right:100px;top:70px;display:flex;gap:58px;font-size:15px;font-weight:700;letter-spacing:.5px}
.hero h1{position:absolute;top:302px;width:100%;text-align:center;font-size:50px;font-weight:400}
.hero p{position:absolute;top:372px;left:140px;width:920px;text-align:center;font-size:22px;font-weight:300;line-height:33px}
.hero-btn{position:absolute;left:481px;top:466px;width:236px;height:51px;border:1px solid rgba(255,255,255,.8);display:flex;align-items:center;justify-content:center;font-size:19px}
.hero-arrow{position:absolute;top:380px;width:20px;height:36px}

/* Clients */
.clients{top:703px;height:282px;text-align:center}
.section-title{font-size:38px;font-weight:300;color:var(--ink)}
.clients .section-title{position:absolute;top:40px;width:100%}
.client-row{position:absolute;top:130px;left:98px;display:flex;gap:16px}
.client{width:152px;height:90px;border:1px solid var(--line);display:flex;align-items:center;justify-content:center;font-size:24px;font-weight:400;color:#4f6478}
.side-arrow{position:absolute;top:158px;width:16px;height:30px}

/* Testimonials */
.testimonials{top:985px;height:363px;background:var(--soft);text-align:center}
.testimonials .section-title{position:absolute;top:56px;width:100%}
.quote{position:absolute;top:132px;left:190px;width:820px;font-size:14px;line-height:22px;color:#3a4148}
.quote-mark{position:absolute;font-size:44px;line-height:44px;color:#b8c1ca;font-family:Georgia,serif}
.avatar{position:absolute;left:570px;top:206px;width:60px;height:60px;border-radius:50%;background:linear-gradient(#5a5f66,#2c3036)}
.author{position:absolute;top:282px;width:100%;font-size:15px}
.author b{color:var(--blue);font-weight:400}

/* Uses */
.uses{top:1348px;height:712px}
.uses h2{position:absolute;top:86px;width:100%;text-align:center;font-size:33px;font-weight:300;line-height:44px;color:#3b4248}
.use{position:absolute;width:470px;display:flex;gap:18px}
.use-icon{flex:none;width:112px;height:112px;border-radius:50%;border:1px solid #cfe6f5;display:flex;align-items:center;justify-content:center}
.use h3{font-size:25px;font-weight:400;margin:10px 0 8px;color:#2e3439}
.use p{font-size:12.5px;line-height:19px;color:var(--muted)}

/* Why us */
.why{top:2060px;height:483px;background:var(--grey);text-align:center}
.why .section-title{position:absolute;top:46px;width:100%}
.reason{position:absolute;top:130px;width:230px}
.reason-icon{width:134px;height:134px;margin:0 auto;border-radius:50%;background:var(--blue);border:5px solid #e6f3fb;box-shadow:0 0 0 2px var(--blue);display:flex;align-items:center;justify-content:center}
.reason h4{margin-top:26px;font-size:14px;font-weight:700;color:#2b3035}
.reason p{margin-top:10px;font-size:12.5px;line-height:19px;color:#444b51}

/* Contact */
.help{top:2543px;height:480px}
.help h2{position:absolute;top:38px;width:100%;text-align:center;font-size:40px;font-weight:300}
.help .lead{position:absolute;top:108px;left:320px;width:560px;text-align:center;font-size:15px;line-height:27px;color:#4a5157}
.field{position:absolute;border:1px solid #c9ced3;font-size:12px;color:#8b9298;padding:14px 16px}
.select-caret{position:absolute;right:16px;top:17px;width:10px;height:8px}
.submit{position:absolute;left:98px;top:356px;width:186px;height:47px;background:var(--blue);color:var(--white);font-size:15px;font-weight:700;display:flex;align-items:center;justify-content:center}
.note{position:absolute;left:108px;top:418px;font-size:10px;color:#555}

/* Footer */
.footer{top:3023px;height:335px;background:var(--blue);color:var(--white)}
.footer h5{font-size:17px;font-weight:400;letter-spacing:.6px}
.col{position:absolute;top:44px}
.links{display:grid;grid-template-columns:138px 160px;row-gap:16px;margin-top:18px;font-size:14px}
.contact-list{margin-top:18px;font-size:14px;line-height:32px;list-style:none}
.contact-list li{display:flex;align-items:center;gap:8px}
.signup p{margin-top:14px;font-size:13px}
.signup-form{display:flex;margin-top:14px}
.signup-input{width:220px;height:40px;border:1px solid rgba(255,255,255,.7);font-size:12px;padding:12px;color:rgba(255,255,255,.8);letter-spacing:.5px}
.signup-btn{width:105px;height:40px;background:#111;font-size:13px;font-weight:700;display:flex;align-items:center;justify-content:center}
.social{display:flex;gap:13px;margin-top:14px}
.social span{width:37px;height:37px;border-radius:50%;background:var(--white)}
.footer-rule{position:absolute;left:98px;top:262px;width:1002px;height:1px;background:rgba(255,255,255,.5)}
.copyright{position:absolute;left:98px;top:286px;font-size:13px}
</style>
</head>
<body>

<header class="hero">
  <div class="hero-photo" role="img" aria-label="Blurred photo of a person reading data on a tablet, washed in bright blue"></div>
  <div class="brand"><span class="brand-mark"></span>quorvix</div>
  <nav class="nav"><span>SOLUTIONS</span><span>PRICING</span><span>COMPANY</span><span>GET FREE QUOTE</span></nav>
  <h1>Turn Websites Into Structured Data feeds</h1>
  <p>Easily get structured data feeds from any website through our cloud based data as a service<br>platform. No programming ,Servers or Expensive Softwares required.</p>
  <div class="hero-btn">GET FREE QUOTE</div>
  <svg class="hero-arrow" style="left:30px" viewBox="0 0 20 36"><path d="M16 2 3 18l13 16" fill="none" stroke="rgba(255,255,255,.6)" stroke-width="2"/></svg>
  <svg class="hero-arrow" style="right:30px" viewBox="0 0 20 36"><path d="M4 2l13 16L4 34" fill="none" stroke="rgba(255,255,255,.6)" stroke-width="2"/></svg>
</header>

<section class="clients">
  <h2 class="section-title">Our Clients</h2>
  <svg class="side-arrow" style="left:58px" viewBox="0 0 16 30"><path d="M13 2 3 15l10 13" fill="none" stroke="#9aa3ab" stroke-width="3"/></svg>
  <div class="client-row">
    <div class="client">Norvane</div>
    <div class="client">Kickpath</div>
    <div class="client">Taskline</div>
    <div class="client">Veltrano</div>
    <div class="client">Brevix</div>
    <div class="client">Zumera</div>
  </div>
  <svg class="side-arrow" style="right:58px" viewBox="0 0 16 30"><path d="M3 2l10 13L3 28" fill="none" stroke="#9aa3ab" stroke-width="3"/></svg>
</section>

<section class="testimonials">
  <h2 class="section-title">Testimonials</h2>
  <svg class="side-arrow" style="left:96px;top:150px" viewBox="0 0 16 30"><path d="M13 2 3 15l10 13" fill="none" stroke="#c5ccd3" stroke-width="2"/></svg>
  <span class="quote-mark" style="left:158px;top:118px">&ldquo;</span>
  <p class="quote">"Quorvix provided us with great service and interactions in a very short amount of time. Even though it was not obvious to extract the data, Quorvix managed to find a way to build a specific crawler that did the job. We couldn't be more satisfied, I am happy with their web scraping services".</p>
  <span class="quote-mark" style="left:676px;top:180px">&rdquo;</span>
  <div class="avatar" role="img" aria-label="Portrait of the client quoted"></div>
  <p class="author"><b>- Marek Elwin</b> - CEO&amp;Founder @Veltrano</p>
  <svg class="side-arrow" style="right:96px;top:150px" viewBox="0 0 16 30"><path d="M3 2l10 13L3 28" fill="none" stroke="#c5ccd3" stroke-width="2"/></svg>
</section>

<section class="uses">
  <h2>Businesses of all sizes use our clean data feeds to Quickly build apps,<br>Experiment with fresh ideas and Solve business problems.</h2>

  <div class="use" style="left:98px;top:208px">
    <div class="use-icon"><svg width="54" height="44" viewBox="0 0 54 44"><rect x="8" y="4" width="38" height="26" fill="none" stroke="#139fe0" stroke-width="3"/><path d="M2 36h50" stroke="#139fe0" stroke-width="4"/></svg></div>
    <div><h3>ECommerce</h3><p>Our Ecommerce product data feeds gives you access to structured product information like pricing, Category, reviews etc. about your competitors.</p></div>
  </div>
  <div class="use" style="left:627px;top:208px">
    <div class="use-icon"><svg width="52" height="52" viewBox="0 0 52 52"><circle cx="26" cy="26" r="22" fill="none" stroke="#139fe0" stroke-width="3"/><circle cx="26" cy="26" r="13" fill="none" stroke="#139fe0" stroke-width="3"/><circle cx="26" cy="26" r="4" fill="#139fe0"/></svg></div>
    <div><h3>Lead generation</h3><p>We help find quality leads for your business by extracting public data from all kind of sources like Linkora, Fundbase, Seedlist etc.</p></div>
  </div>
  <div class="use" style="left:98px;top:372px">
    <div class="use-icon"><svg width="54" height="54" viewBox="0 0 54 54"><g stroke="#139fe0" stroke-width="3"><path d="M27 27 8 10M27 27l19-17M27 27 8 44M27 27l19 17"/></g><g fill="#139fe0"><circle cx="27" cy="27" r="8"/><circle cx="8" cy="10" r="6"/><circle cx="46" cy="10" r="6"/><circle cx="8" cy="44" r="6"/><circle cx="46" cy="44" r="6"/></g></svg></div>
    <div><h3>SERP Tracking</h3><p>Our SERP data feeds gives companies access to Search Engine rankings of any keywords from search engines like Findly, Yoodle and Sarch.</p></div>
  </div>
  <div class="use" style="left:627px;top:372px">
    <div class="use-icon"><svg width="44" height="48" viewBox="0 0 44 48"><g fill="none" stroke="#139fe0" stroke-width="3"><path d="M4 30v14h36V30"/><path d="M12 36h20M14 26h20M16 16h20M20 6h18"/></g></svg></div>
    <div><h3>News Aggregation</h3><p>We help businesses build their own unique news data feeds by aggregating data from news sites, industry blogs etc.</p></div>
  </div>
  <div class="use" style="left:98px;top:537px">
    <div class="use-icon"><svg width="50" height="50" viewBox="0 0 50 50"><rect x="17" y="4" width="16" height="26" fill="#139fe0"/><path d="M4 34q10 0 16 6h26v4H18q-6-4-14-4z" fill="#139fe0"/></svg></div>
    <div><h3>Recruiting</h3><p>We help recruiters automate scouting candidate profiles from different online sources and speed up hiring process.</p></div>
  </div>
  <div class="use" style="left:627px;top:537px">
    <div class="use-icon"><svg width="50" height="50" viewBox="0 0 50 50"><circle cx="25" cy="25" r="9" fill="none" stroke="#139fe0" stroke-width="6" stroke-dasharray="5 3"/><circle cx="25" cy="25" r="16" fill="none" stroke="#139fe0" stroke-width="3"/></svg></div>
    <div><h3>Build your App</h3><p>We help businesses quickly build their apps on top of our scalable data extraction infrastructure.</p></div>
  </div>
</section>

<section class="why">
  <h2 class="section-title">Why Us</h2>
  <div class="reason" style="left:98px">
    <div class="reason-icon"><svg width="50" height="62" viewBox="0 0 50 62"><g fill="none" stroke="#fff" stroke-width="3"><path d="M17 42v-6Q7 30 7 20a18 18 0 0 1 36 0q0 10-10 16v6z"/><path d="M18 48h14M20 54h10"/></g></svg></div>
    <h4>SOLVE REAL PROBLEMS</h4>
    <p>Quorvix provides a fully managed Big Data As A Service. You can easily plug our data feeds into your favourite tool and start solving the real problems. Focus on growing your business while we take care of the data extraction.</p>
  </div>
  <div class="reason" style="left:355px">
    <div class="reason-icon"><svg width="58" height="62" viewBox="0 0 58 62"><g fill="#fff"><ellipse cx="24" cy="10" rx="20" ry="7"/><path d="M4 16q20 10 40 0v10q-20 10-40 0zM4 32q20 10 40 0v10q-20 10-40 0z"/></g><circle cx="44" cy="46" r="11" fill="#fff"/><path d="m38 46 4 4 8-8" fill="none" stroke="#139fe0" stroke-width="3"/></svg></div>
    <h4>CLEAN DATA</h4>
    <p>We follow a strict quality assurance process and a Machine learning based QA system to ensure the data integrity. You can export data as CSV / JSON files, XML feeds or use our APIs to plug the data right into your tools.</p>
  </div>
  <div class="reason" style="left:615px">
    <div class="reason-icon"><svg width="64" height="50" viewBox="0 0 64 50"><g fill="#fff"><circle cx="22" cy="14" r="10"/><path d="M2 48q0-20 20-20t20 20z"/><circle cx="44" cy="12" r="8"/><path d="M46 26q16 2 16 20H46q0-12-6-18z"/></g></svg></div>
    <h4>CUSTOMER SUCCESS</h4>
    <p>Ensuring Customer success is our first priority. Our customer success team consists of experienced data mining engineers and they are equipped with modern tools. They will work directly with you to make sure that you get what you asked for</p>
  </div>
  <div class="reason" style="left:872px">
    <div class="reason-icon"><svg width="48" height="58" viewBox="0 0 48 58"><g fill="none" stroke="#fff" stroke-width="3"><path d="M4 2h28l12 12v42H4z"/><path d="M12 20h20M12 28h24M12 36h14"/><path d="m28 44 4 4 8-8"/></g></svg></div>
    <h4>DATA WRANGLING SUPPORT</h4>
    <p>Quorvix helps those who need data wrangling support by providing profiling, filtering and enrichment support. We know Just getting structured data might not solve your problems. Don't spent time learning a new tool, we can help.</p>
  </div>
</section>

<section class="help">
  <h2>We’re here to help!</h2>
  <p class="lead">We're friendly and available to help solve your data extraction problems. Fill the form below to contact us. Let us do the heavy lifting for you</p>
  <div class="field" style="left:98px;top:177px;width:551px;height:45px">Your Email address</div>
  <div class="field" style="left:779px;top:177px;width:321px;height:45px">Your Monthly Budget
    <svg class="select-caret" viewBox="0 0 10 8"><path d="M1 1l4 5 4-5" fill="none" stroke="#8b9298" stroke-width="1.5"/></svg>
  </div>
  <div class="field" style="left:98px;top:251px;width:1002px;height:72px">Your Message</div>
  <div class="submit">SUBMIT MESSAGE</div>
  <p class="note">*Please fill all required form fields, thanks!</p>
</section>

<footer class="footer">
  <div class="col" style="left:98px">
    <h5>QUICK LINKS</h5>
    <div class="links">
      <span>Blog</span><span>Startup Partner program</span>
      <span>Answers</span><span>FAQ</span>
      <span>Case Studies</span><span>Careers</span>
      <span>Slide</span><span>Social media</span>
    </div>
  </div>
  <div class="col" style="left:499px">
    <h5>CONTACT INFO</h5>
    <ul class="contact-list">
      <li>12 Harbor Lane</li>
      <li>City Address, Country Code.</li>
      <li><svg width="14" height="14" viewBox="0 0 14 14"><rect width="14" height="14" rx="3" fill="#fff"/><path d="M4 3l2 2-1 1q1 2 3 3l1-1 2 2-1 1q-5-1-7-6z" fill="#139fe0"/></svg>(01) 555 0147</li>
      <li><svg width="14" height="11" viewBox="0 0 14 11"><rect width="14" height="11" fill="#fff"/><path d="M0 0l7 6 7-6" fill="none" stroke="#139fe0" stroke-width="1.5"/></svg>hello@quorvix.com</li>
    </ul>
  </div>
  <div class="col signup" style="left:772px">
    <h5>SIGN UP FOR NEWSLETTERS</h5>
    <p>Please sign up here for latest news</p>
    <div class="signup-form"><div class="signup-input">EMAIL ADDRESS</div><div class="signup-btn">SUBSCRIBE</div></div>
    <div class="social"><span></span><span></span><span></span><span></span></div>
  </div>
  <div class="footer-rule"></div>
  <p class="copyright">© 2016 Quorvix . All right reserved . Term of Use</p>
</footer>

</body>
</html>
```